design a construction company business card

Design business card around our logo. Card must have all the typical info: name, title, address, phone, email, business name, etc. Somewhere on the card I would like to see our motto "Grounded in craft... Driven by lasting trust." Consider adding a splash of bright orange to the card to complement the blues and silvers/grays in the logo. We are open to metallic inks, textures, etc. We would like to see options on both light and dark backgrounds. The font in the logo is Euro Technic Extended Regular.

```html
<!DOCTYPE html>
<html lang="en">
<head>
<meta charset="utf-8">
<title>Halden Building, Inc. – Business Card</title>
<link rel="stylesheet" href="https://fonts.googleapis.com/css2?family=Lato:wght@300;400;700&family=Oswald:wght@400&display=swap">
<style>
  :root {
    --backdrop: #3a3431;
    --card: #0f0f10;
    --card-edge: #1b1b1d;
    --brand-blue: #2f7fd6;
    --silver: #cfd1d4;
    --text-light: #d9dadc;
    --text-muted: #bfc1c4;
    --divider: #2a2a2d;
  }
  * { margin: 0; padding: 0; box-sizing: border-box; }
  html, body { width: 1200px; height: 844px; overflow: hidden; }
  body {
    background: var(--backdrop);
    position: relative;
    font-family: "Lato", Arial, sans-serif;
  }
  .card {
    position: absolute;
    width: 520px;
    height: 298px;
    background: var(--card);
    border: 1px solid var(--card-edge);
    top: 273px;
  }

  /* Contact side */
  .card--contact { left: 50px; }
  .card--contact .brand {
    position: absolute;
    left: 40px;
    top: 110px;
    width: 220px;
    display: flex;
    align-items: center;
    gap: 12px;
  }
  .brand__mark {
    width: 18px; height: 18px; flex: none;
    background: var(--brand-blue);
  }
  .brand__name {
    color: var(--brand-blue);
    font-weight: 700;
    line-height: 1.05;
  }
  .card--contact .brand__name .line-main { display: block; font-size: 34px; letter-spacing: 3px; }
  .card--contact .brand__name .line-sub { display: block; font-size: 13px; letter-spacing: 2px; margin-top: 4px; }
  .card--contact .divider {
    position: absolute;
    left: 285px; top: 36px;
    width: 1px; height: 226px;
    background: var(--divider);
  }
  .contact {
    position: absolute;
    left: 305px;
    top: 56px;
    color: var(--text-light);
  }
  .contact__name {
    color: var(--brand-blue);
    font-size: 15px;
    font-weight: 300;
    letter-spacing: 1.5px;
    text-transform: uppercase;
  }
  .contact__title { font-size: 14px; margin-bottom: 4px; }
  .contact__list { list-style: none; font-size: 13.5px; }
  .contact__list li { display: flex; align-items: flex-start; gap: 8px; line-height: 1.5; }
  .contact__list svg { width: 11px; height: 11px; margin-top: 5px; flex: none; fill: var(--text-muted); }
  .contact__list .address { margin-top: 4px; }

  /* Brand side */
  .card--brand { left: 630px; }
  .card--brand .brand-block {
    position: absolute;
    left: 60px; right: 60px;
    top: 70px;
    text-align: center;
  }
  .card--brand .rule { height: 1px; background: var(--silver); opacity: .7; }
  .card--brand .brand {
    display: flex; align-items: center; justify-content: center;
    gap: 14px; padding: 14px 0 12px;
  }
  .card--brand .brand__mark { background: var(--silver); width: 20px; height: 20px; }
  .card--brand .brand__name { color: var(--silver); text-align: left; }
  .card--brand .brand__name .line-main { display: block; font-size: 44px; letter-spacing: 4px; }
  .card--brand .brand__name .line-sub { display: block; font-size: 15px; letter-spacing: 3px; margin-top: 4px; }
  .motto {
    font-family: "Oswald", "Arial Narrow", sans-serif;
    color: #ffffff;
    font-size: 13px;
    letter-spacing: .6px;
    text-transform: uppercase;
    margin-top: 12px;
    padding-top: 8px;
    border-top: 1px solid #8d8f92;
  }
</style>
</head>
<body>

  <section class="card card--contact" aria-label="Business card, contact side">
    <div class="brand">
      <span class="brand__mark" aria-hidden="true"></span>
      <span class="brand__name"><span class="line-main">HALDEN</span><span class="line-sub">BUILDING, INC.</span></span>
    </div>
    <div class="divider" aria-hidden="true"></div>
    <div class="contact">
      <p class="contact__name">Marcus Delane</p>
      <p class="contact__title">Managing Director</p>
      <ul class="contact__list">
        <li><svg viewBox="0 0 12 12" aria-hidden="true"><path d="M2.5 0.8 4.4 3 3.5 4.3c.7 1.6 2.1 3 3.7 3.7L8.5 7l2.2 1.9-1.1 2.1C5 10.8 1 6.8.8 2.3z"/></svg>055-987 210 346</li>
        <li><svg viewBox="0 0 12 12" aria-hidden="true"><path d="M0 2h12v8H0z M1 3l5 3.6L11 3v-.2H1z" fill-rule="evenodd"/></svg>hello@haldenbuild.com</li>
        <li><svg viewBox="0 0 12 12" aria-hidden="true"><circle cx="6" cy="6" r="5.5"/></svg>www.haldenbuild.com</li>
        <li class="address">318, Foundry Row West,<br>60218, Easton Vale</li>
      </ul>
    </div>
  </section>

  <section class="card card--brand" aria-label="Business card, brand side">
    <div class="brand-block">
      <div class="rule" aria-hidden="true"></div>
      <div class="brand">
        <span class="brand__mark" aria-hidden="true"></span>
        <span class="brand__name"><span class="line-main">HALDEN</span><span class="line-sub">BUILDING, INC.</span></span>
      </div>
      <p class="motto">Grounded in craft... Driven by lasting trust</p>
    </div>
  </section>

</body>
</html>
```